VFX Company Business Card Design Project

The Kestrel Works is a decentralized Visual Effects Studio servicing the television and feature film industries.
Project Brief:
Take our logo that was previously designed on Pencil Harbor and make a double sided business card.
Requirements:
- Card MUST be double sided.
- Front of card MUST have the yellow part of our logo against the dark grey background.
- Back of card is completely up to the designer.
- Back of card must include the complete company logo.
Please follow these File Preparation guidelines:
http://printnook.ca/infopage?file=filetype_en&s=PrintNook_new&lang=en
Business

```html
<!DOCTYPE html>
<html lang="en">
<head>
<meta charset="utf-8">
<title>The Kestrel Works – Business Card</title>
<link rel="stylesheet" href="https://fonts.googleapis.com/css2?family=Josefin+Sans:wght@400;600&family=Open+Sans:wght@400;700&display=swap">
<style>
  :root {
    --backdrop: #8a4a22;
    --card: #2b2b2b;
    --gold: #fcc32a;
    --ink-light: #eef0e6;
    --ink-soft: #e4e4e0;
  }
  html, body {
    margin: 0;
    padding: 0;
    width: 1200px;
    height: 734px;
    overflow: hidden;
    background: var(--backdrop);
  }
  .sheet {
    position: relative;
    width: 1200px;
    height: 734px;
  }
  .card {
    position: absolute;
    width: 524px;
    height: 300px;
    background: var(--card);
    box-sizing: border-box;
    display: flex;
    flex-direction: column;
    align-items: center;
    justify-content: center;
    font-family: "Josefin Sans", sans-serif;
    color: var(--ink-soft);
  }
  .card--front    { left: 67px;  top: 43px; }
  .card--contact  { left: 628px; top: 48px; justify-content: flex-start; padding-top: 74px; }
  .card--lockup   { left: 64px;  top: 381px; }
  .card--wordmark { left: 622px; top: 387px; }

  .brand-name {
    margin: 0;
    font-family: "Josefin Sans", sans-serif;
    font-weight: 600;
    line-height: 1;
    letter-spacing: 0.5px;
    white-space: nowrap;
  }
  .brand-name--front    { color: var(--gold); font-size: 54px; }
  .brand-name--contact  { color: var(--ink-light); font-size: 46px; }
  .brand-name--lockup   { color: var(--ink-light); font-size: 36px; }
  .brand-name--wordmark { color: var(--ink-light); font-size: 52px; margin-top: -30px; }

  .lockup {
    display: flex;
    align-items: center;
    gap: 18px;
    margin-top: -40px;
  }
  .lockup__dot {
    width: 44px;
    height: 44px;
    border-radius: 50%;
    background: var(--gold);
  }

  .web {
    position: absolute;
    bottom: 26px;
    left: 0;
    right: 0;
    text-align: center;
    font-size: 18px;
    letter-spacing: 3px;
    color: var(--ink-soft);
  }

  .person {
    margin: 58px 0 0;
    font-family: "Open Sans", sans-serif;
    font-size: 17px;
    color: var(--ink-soft);
  }
  .person__name { font-weight: 700; }
  .person__title { font-size: 13px; }

  .contact-row {
    display: flex;
    align-items: center;
    gap: 12px;
    margin-top: 12px;
    font-family: "Open Sans", sans-serif;
    font-size: 13px;
    color: var(--ink-soft);
  }
  .contact-item {
    display: flex;
    align-items: center;
    gap: 5px;
  }
  .contact-item svg { width: 11px; height: 11px; fill: var(--ink-soft); }
  .address {
    margin-top: 14px;
    font-family: "Open Sans", sans-serif;
    font-size: 13px;
    letter-spacing: 1px;
    color: var(--ink-soft);
  }
</style>
</head>
<body>
<main class="sheet">

  <section class="card card--front" aria-label="Card front">
    <p class="brand-name brand-name--front">The Kestrel Works</p>
  </section>

  <section class="card card--contact" aria-label="Card back with contact details">
    <p class="brand-name brand-name--contact">The Kestrel Works</p>
    <p class="person"><span class="person__name">Your Name,</span> <span class="person__title">Title</span></p>
    <div class="contact-row">
      <span class="contact-item">
        <svg viewBox="0 0 12 12" aria-hidden="true"><path d="M2.5 1l2 2.2-1 1.3c.7 1.5 2 2.8 3.5 3.5l1.3-1 2.2 2-1.2 1.8C5.5 10.5 1.5 6.5.8 2.3z"/></svg>
        0987 654321
      </span>
      <span class="contact-item">
        <svg viewBox="0 0 12 12" aria-hidden="true"><rect x="3" y="0.5" width="6" height="11" rx="1"/></svg>
        0987 654321
      </span>
      <span class="contact-item">
        <svg viewBox="0 0 12 12" aria-hidden="true"><path d="M0.5 3h11v7h-11z M1 3.3l5 4 5-4" stroke="#2b2b2b" stroke-width="0.8"/></svg>
        info@kestrelworks.com
      </span>
    </div>
    <div class="contact-row">
      <span class="contact-item">
        <svg viewBox="0 0 12 12" aria-hidden="true"><circle cx="6" cy="6" r="5.5"/><path d="M0.5 6h11M6 .5v11M2 3h8M2 9h8" stroke="#2b2b2b" stroke-width="0.8" fill="none"/></svg>
        www.kestrelworks.com
      </span>
    </div>
    <p class="address">00, Complex name, City, State 0042</p>
  </section>

  <section class="card card--lockup" aria-label="Card back with brand lockup">
    <div class="lockup">
      <span class="lockup__dot"></span>
      <p class="brand-name brand-name--lockup">The Kestrel Works</p>
    </div>
    <p class="web">www.kestrelworks.com</p>
  </section>

  <section class="card card--wordmark" aria-label="Card back with wordmark">
    <p class="brand-name brand-name--wordmark">The Kestrel Works</p>
    <p class="web">www.kestrelworks.com</p>
  </section>

</main>
</body>
</html>
```